Business Card for Multi-Brand Sportswear Company

We are looking for a business card which represents our company and the multiple brands within it.

The company: Fen Athletics (LTD)
The brands: Fen, TavaPuni, ElmStretch, Grit and Rain

Employees using these cards would be representing Fen Athletics, rather than any of the individual brands. You will see a current design within the uploaded files, to give some inspiration. The actual text of the brands is not necessary, but the logos should be on there is some format.

Our creative minds on this are stretched, so we are looking for someone to make this their own, and show us what a good business card should look like.

We may like to get these printed with spot gloss, so keep that in mind with your designs.

www.fenathletics.co.uk

Industry/Entity Type

Business

Contact Information for Business Card

Leo Pemberton-Hale
Operations Manager
(+44) 1632 960 418
Leo@fenathletics.co.uk
www.fenathletics.co.uk

Font styles to use
Sans Serif
Other font styles liked:
• Eurostile

Colors
ffffff

Requirements
Nice to have
• Dark (black) background

```html
<!DOCTYPE html>
<html lang="en">
<head>
<meta charset="utf-8">
<title>Fen Athletics Business Card</title>
<link rel="stylesheet" href="https://fonts.googleapis.com/css2?family=Michroma&family=Open+Sans:wght@400;600;700&display=swap">
<style>
  :root {
    --backdrop: #3a332f;
    --card-white: #ffffff;
    --card-black: #1f1f1f;
    --panel-grey: #d9d9d9;
    --ink: #1a1a1a;
    --ink-soft: #6b6b6b;
    --text-light: #d6d6d6;
    --accent-red: #e0201f;
    --brand-tile: #cfcfcf;
  }
  * { box-sizing: border-box; margin: 0; padding: 0; }
  html, body { width: 1200px; height: 716px; overflow: hidden; }
  body {
    background: var(--backdrop);
    font-family: "Open Sans", sans-serif;
    position: relative;
  }
  .card {
    position: absolute;
    top: 198px;
    width: 530px;
    height: 320px;
    overflow: hidden;
    box-shadow: 0 14px 30px rgba(0,0,0,.45);
  }
  .card--front { left: 45px; background: var(--card-white); }
  .card--back { left: 625px; background: var(--card-black); }

  /* wordmark */
  .wordmark { text-align: center; color: var(--ink); }
  .wordmark__name {
    font-family: "Open Sans", sans-serif;
    font-weight: 700;
    font-size: 34px;
    letter-spacing: 1px;
    text-transform: uppercase;
    line-height: 1;
  }
  .wordmark__rule { height: 2px; background: var(--ink-soft); margin: 8px 0 5px; }
  .wordmark__tagline {
    font-size: 8px; font-weight: 600; letter-spacing: 2px;
    text-align: right; color: var(--ink);
  }

  .brands { display: flex; gap: 14px; justify-content: center; margin-top: 14px; }
  .brand { display: flex; align-items: center; gap: 5px; font-size: 10px; font-weight: 600; color: var(--ink); white-space: nowrap; }
  .brand__mark { width: 12px; height: 12px; background: var(--brand-tile); border-radius: 2px; }

  .card--front .logo-block { position: absolute; left: 95px; top: 88px; width: 340px; }

  .front-band { position: absolute; left: 0; right: 0; bottom: 0; height: 22px; background: var(--ink); }
  .front-band__red { position: absolute; left: 0; top: 0; width: 42%; height: 8px; background: var(--accent-red); }

  /* back */
  .panel {
    position: absolute; left: 0; top: 0; width: 270px; height: 150px;
    background: var(--panel-grey); border-bottom-right-radius: 10px;
    padding: 26px 18px 0;
  }
  .panel .wordmark__name { font-size: 24px; }
  .panel .wordmark__rule { margin: 6px 0 4px; }
  .panel .brands { gap: 6px; margin-top: 10px; }
  .panel .brand { font-size: 7.5px; gap: 3px; }
  .panel .brand__mark { width: 9px; height: 9px; background: #a8a8a8; }

  .company-line {
    position: absolute; left: 18px; top: 160px;
    font-family: "Michroma", sans-serif; font-size: 12px; letter-spacing: 3px;
    color: var(--text-light); text-transform: uppercase;
  }
  .person { position: absolute; left: 30px; top: 196px; color: var(--text-light); }
  .person__name { font-size: 15px; font-weight: 600; }
  .person__role { font-size: 11px; margin-left: 48px; color: #bdbdbd; }

  .contact { position: absolute; right: 30px; top: 150px; width: 210px; color: var(--text-light); font-size: 12px; line-height: 1.45; }
  .contact__web { letter-spacing: 2px; margin-bottom: 18px; }
  .contact__address { margin-bottom: 12px; }

  .back-band { position: absolute; left: 0; right: 0; bottom: 10px; height: 10px; }
  .back-band__red { position: absolute; left: 0; top: 0; width: 48%; height: 100%; background: var(--accent-red); }
  .back-band__white { position: absolute; left: 48%; right: 0; top: 0; height: 100%; background: var(--card-white); }
</style>
</head>
<body>

<section class="card card--front" aria-label="Card front">
  <div class="logo-block">
    <div class="wordmark">
      <div class="wordmark__name">Fen Athletics</div>
      <div class="wordmark__rule"></div>
      <div class="wordmark__tagline">PERFORMANCE WEAR</div>
    </div>
    <div class="brands">
      <span class="brand"><span class="brand__mark"></span>TavaPuni</span>
      <span class="brand"><span class="brand__mark"></span>ElmStretch</span>
      <span class="brand"><span class="brand__mark"></span>Grit and Rain</span>
      <span class="brand"><span class="brand__mark"></span>Fen</span>
    </div>
  </div>
  <div class="front-band"><div class="front-band__red"></div></div>
</section>

<section class="card card--back" aria-label="Card back">
  <div class="panel">
    <div class="wordmark">
      <div class="wordmark__name">Fen Athletics</div>
      <div class="wordmark__rule"></div>
      <div class="wordmark__tagline">PERFORMANCE WEAR</div>
    </div>
    <div class="brands">
      <span class="brand"><span class="brand__mark"></span>TavaPuni</span>
      <span class="brand"><span class="brand__mark"></span>ElmStretch</span>
      <span class="brand"><span class="brand__mark"></span>Grit and Rain</span>
      <span class="brand"><span class="brand__mark"></span>Fen</span>
    </div>
  </div>
  <div class="company-line">Fen Athletics (LTD)</div>
  <div class="person">
    <div class="person__name">Leo Pemberton-Hale</div>
    <div class="person__role">Operations Manager</div>
  </div>
  <div class="contact">
    <div class="contact__web">www.fenathletics.co.uk</div>
    <div class="contact__address">Kestrel Court, Ashwell,<br>Hollby, HB4 9QT</div>
    <div>(+44) 1632 960 418</div>
    <div>Leo@fenathletics.co.uk</div>
  </div>
  <div class="back-band"><div class="back-band__red"></div><div class="back-band__white"></div></div>
</section>

</body>
</html>
```